Business card for Sports Apparel business

DOUBLE SIDED DESIGN
We need business cards for a new sports apparel business. We are developing a protective headband for soccer initially.
Torvalle is focused on designing and developing head protection products to reduce the likelihood of concussion when playing sports. Exploring and understanding medical insights, material science research, current and former players experiences and governing bodies guidelines has allowed Torvalle to develop the safety, style, form and function requirements of a suitable product to bring to market.
Target Market(s)
Mums buying kits for the sons and daughters. Amateur footballers.
Industry/Entity Type
Sporting Good
Contact Information for Business Card
Martin Ashworth - CEO
Mobile: +44 7431589027
Email: martin@torvalle.co.uk
Tel: 0208 5519372
Helena Pargeter - COO
Mob: +44 7385 640117
Email: helena@torvalle.co.uk
Tel: 0208 5519372
Duncan Farrow - CCO
Mob: +44 7564 293081
Email: duncan@torvalle.co.uk
Tel: 0208 5519372
Look and feel
Each slider illustrates characteristics of the customer's brand and the style your logo design should communicate.

```html
<!DOCTYPE html>
<html lang="en">
<head>
<meta charset="utf-8">
<title>Torvalle Business Card</title>
<link href="https://fonts.googleapis.com/css2?family=Montserrat:wght@400;600;700&display=swap" rel="stylesheet">
<style>
  :root {
    --brand-blue: #0b5b96;
    --card-white: #ffffff;
    --ink-grey: #55585c;
    --stage: #2a2a2c;
  }
  * { margin: 0; padding: 0; box-sizing: border-box; }
  html, body {
    width: 1200px; height: 852px; overflow: hidden;
    background: var(--stage);
    font-family: "Montserrat", sans-serif;
  }
  .stage {
    width: 1200px; height: 852px;
    display: flex; flex-direction: column; align-items: center; justify-content: center;
    gap: 40px;
  }
  .card {
    position: relative;
    width: 600px; height: 343px;
    border-radius: 18px;
    overflow: hidden;
  }
  .card-front {
    background: var(--brand-blue);
    display: flex; align-items: center; justify-content: center;
  }
  .wordmark {
    font-weight: 700;
    letter-spacing: 3px;
    text-transform: uppercase;
  }
  .card-front .wordmark { color: var(--card-white); font-size: 52px; }
  .card-back { background: var(--card-white); }
  .back-band { position: absolute; inset: 0; width: 100%; height: 100%; }
  .card-back .wordmark {
    position: absolute; left: 40px; top: 72px;
    color: var(--ink-grey); font-size: 36px;
  }
  .person {
    position: absolute; right: 34px; top: 168px;
    text-align: right; color: var(--card-white);
  }
  .person-name { font-size: 19px; font-weight: 600; letter-spacing: 0.5px; text-transform: uppercase; }
  .person-role { font-size: 12px; margin-top: 2px; }
  .links {
    position: absolute; right: 34px; top: 236px;
    color: var(--card-white); font-size: 14px; text-align: right;
    display: flex; flex-direction: column; gap: 6px;
  }
  .phones {
    position: absolute; left: 40px; bottom: 34px;
    color: var(--card-white); font-size: 15px;
    display: flex; flex-direction: column; gap: 6px;
  }
  .line { display: flex; align-items: center; gap: 8px; }
  .links .line { justify-content: flex-end; }
  .icon { width: 13px; height: 13px; flex: none; }
</style>
</head>
<body>
<main class="stage">
  <section class="card card-front">
    <span class="wordmark">Torvalle</span>
  </section>

  <section class="card card-back">
    <svg class="back-band" viewBox="0 0 600 343" preserveAspectRatio="none" aria-hidden="true">
      <path d="M0 152 H22 L30 140 H56 L62 152 H534 L542 140 H566 L572 152 H600 V343 H0 Z" fill="var(--brand-blue)"/>
    </svg>

    <span class="wordmark">Torvalle</span>

    <div class="person">
      <div class="person-name">Martin Ashworth</div>
      <div class="person-role">CEO</div>
    </div>

    <div class="links">
      <div class="line">martin@torvalle.co.uk
        <svg class="icon" viewBox="0 0 14 14" fill="none" stroke="#fff" stroke-width="1.4"><rect x="1" y="3" width="12" height="8"/><path d="M1 3 L7 8 L13 3"/></svg>
      </div>
      <div class="line">www.torvalle.co.uk
        <svg class="icon" viewBox="0 0 14 14" fill="none" stroke="#fff" stroke-width="1.2"><circle cx="7" cy="7" r="6"/><ellipse cx="7" cy="7" rx="2.6" ry="6"/><path d="M1 7 H13"/></svg>
      </div>
    </div>

    <div class="phones">
      <div class="line">
        <svg class="icon" viewBox="0 0 14 14" fill="#fff"><path d="M3 1 L5.5 1 L6.5 4 L5 5.2 C5.8 7 7 8.2 8.8 9 L10 7.5 L13 8.5 L13 11 C13 12 12 13 11 13 C5.5 12.5 1.5 8.5 1 3 C1 2 2 1 3 1 Z"/></svg>
        0208 5519372
      </div>
      <div class="line">
        <svg class="icon" viewBox="0 0 14 14" fill="none" stroke="#fff" stroke-width="1.3"><rect x="3.5" y="1" width="7" height="12" rx="1.2"/><path d="M6 11 H8"/></svg>
        +44 7431589027
      </div>
    </div>
  </section>
</main>
</body>
</html>
```